Website design for luxury private hair salon

I'm looking for someone to use my Logo and build me a website for my webpage www.corsetresses.com.au (You can have a look at it as it has every detail I need included on it already), however I want a fresh new appearance and it to look and feel super stylish.

I am thinking colours in black, with silver or white, beautiful hair images like the ones you'll see on the current webpage - the price list as per what you already see.

I will include a copy of my biz card on here, so you can see the feel of the card, and design a website with a similar feel. It is matt black with a foil silver.

Modern, but classic and fresh. I will also need you to be able to publish it to my URL for me as I have no idea how to do this. I need it up and running pronto!

The website will need to be able to be read clearly on all devices incluing smart phones and ipads. The URL is currently registered and hosted by Norvel Web

Thinking a Home Page - large logo etc and write up on who and what we offer
Services/Price List page - as per the price list on my current webpage
Contact Page - with a built in contact form.

Target Market(s)

Middle aged, fashionable, stylish women and men who enjoy luxury hair care and styling in an upmarket location.

Industry/Entity Type

Hair And Beauty

Number of Pages Required

3 page

Font styles to use
Other font styles liked:
• see my images for my current logo

Colors
000000
b2b2b2
a54499

Requirements
Must have
• Style
• Fast turnaround
• Be viewable on all devices, PC, ipads, smart phones
• Designer able to upload it so its a running website for me to my URL
Nice to have
• Just a really feminine, stylish website which is easy to read and shows some beautiful images of perfect hair
Should not have
• Browns, reds or orange colours.

```html
<!DOCTYPE html>
<html lang="en">
<head>
<meta charset="utf-8">
<title>Corsetresses hair &amp; body — Contact Us</title>
<link rel="stylesheet" href="https://fonts.googleapis.com/css2?family=Cinzel:wght@500;600&family=Lato:wght@400;700&family=Merriweather:wght@300&display=swap">
<style>
  :root {
    --black: #111111;
    --ink: #2b2b2b;
    --silver: #d4d4d4;
    --grey: #b2b2b2;
    --muted: #9a9a9a;
    --plum: #a54499;
    --plum-deep: #2a0f35;
    --field-line: #e2e2e2;
    --white: #ffffff;
  }
  * { box-sizing: border-box; margin: 0; padding: 0; }
  html, body { width: 670px; height: 1200px; overflow: hidden; background: var(--white); }
  .page { position: relative; width: 670px; height: 1200px; overflow: hidden; font-family: "Lato", sans-serif; color: var(--ink); }

  .masthead { position: absolute; left: 0; top: 0; width: 670px; height: 314px; background: var(--black); }
  .main-nav { position: absolute; top: 48px; left: 0; width: 100%; display: flex; justify-content: center; gap: 10px; }
  .main-nav a { color: var(--white); text-decoration: none; font-size: 8px; letter-spacing: 0.1px; padding-bottom: 3px; }
  .main-nav a.is-current { border-bottom: 1px solid var(--white); }
  .brand { position: absolute; top: 100px; left: 0; width: 100%; text-align: center; font-family: "Cinzel", serif; font-weight: 500; color: var(--silver); }
  .brand-name { display: block; font-size: 62px; letter-spacing: 2px; line-height: 1; }
  .brand-tag { display: block; font-size: 26px; letter-spacing: 3px; margin-top: 26px; text-transform: lowercase; }

  .section-title { position: absolute; top: 352px; width: 100%; text-align: center; font-family: "Cinzel", serif; font-weight: 600; font-size: 24px; letter-spacing: 5px; color: var(--ink); }

  .banner { position: absolute; top: 410px; left: 0; width: 670px; height: 160px;
    background: radial-gradient(ellipse at 62% 50%, #a2467f 0%, #5a2466 28%, #2c1240 58%, #140a1f 100%); }

  .contact-form .field { position: absolute; border: 1px solid var(--field-line); background: var(--white);
    font-family: "Merriweather", serif; font-weight: 300; font-size: 7px; color: #777; padding: 7px 6px; line-height: 1.3; }
  .field-name { left: 120px; top: 618px; width: 135px; height: 26px; }
  .field-email { left: 270px; top: 618px; width: 135px; height: 26px; }
  .field-phone { left: 420px; top: 618px; width: 134px; height: 26px; padding-top: 5px !important; }
  .field-message { left: 120px; top: 662px; width: 434px; height: 56px; }
  .send-button { position: absolute; left: 291px; top: 733px; width: 89px; height: 29px; background: var(--plum); color: var(--white);
    font-size: 9px; font-weight: 700; display: flex; align-items: center; justify-content: center; letter-spacing: 0.3px; }

  .location { position: absolute; top: 880px; width: 100%; text-align: center; font-family: "Cinzel", serif; font-weight: 600; color: var(--ink); }
  .location-name { font-size: 23px; letter-spacing: 5px; }
  .location-rule { width: 420px; height: 2px; background: var(--ink); margin: 6px auto 4px; }
  .location-phones { font-size: 17px; letter-spacing: 1.5px; }

  .details { position: absolute; top: 1000px; width: 100%; text-align: center; font-family: "Cinzel", serif; font-weight: 600; color: var(--ink); }
  .details-note { font-size: 13px; letter-spacing: 0.5px; }
  .details-links { margin-top: 11px; font-size: 12px; letter-spacing: 1px; word-spacing: 2px; }
  .details-links span + span { margin-left: 20px; }

  .site-footer { position: absolute; top: 1120px; left: 0; width: 670px; height: 50px; }
  .footer-copy { position: absolute; left: 94px; top: 10px; font-family: "Merriweather", serif; font-weight: 300; font-size: 6px; color: var(--grey); line-height: 1.9; }
  .footer-brand { position: absolute; left: 0; width: 100%; top: 6px; text-align: center; font-family: "Cinzel", serif; font-weight: 500; color: var(--ink); }
  .footer-brand .brand-name { font-size: 20px; letter-spacing: 1px; }
  .footer-brand .brand-tag { font-size: 8px; letter-spacing: 1px; margin-top: 1px; text-transform: lowercase; }
  .social-links { position: absolute; left: 512px; top: 10px; display: flex; gap: 6px; }
  .social-links span { width: 18px; height: 18px; border: 1.5px solid var(--plum); display: block; }
  .back-to-top { position: absolute; left: 625px; top: 1158px; }
</style>
</head>
<body>
<div class="page">
  <header class="masthead">
    <nav class="main-nav">
      <a href="#">HOME</a>
      <a href="#">PRICE LIST</a>
      <a href="#" class="is-current">CONTACT US</a>
    </nav>
    <div class="brand">
      <span class="brand-name">Corsetresses</span>
      <span class="brand-tag">hair &amp; body</span>
    </div>
  </header>

  <h1 class="section-title">Contact Us</h1>

  <div class="banner" role="img" aria-label="Portrait photograph of a woman with styled hair in a fur collar, purple tones"></div>

  <form class="contact-form">
    <div class="field field-name">May we know your name?</div>
    <div class="field field-email">What is your email address?</div>
    <div class="field field-phone">Or if you'd prefer we call you, let us know your number here...</div>
    <div class="field field-message">What can we help you with?</div>
    <div class="send-button">SEND</div>
  </form>

  <section class="location">
    <div class="location-name">Hillcrest</div>
    <div class="location-rule"></div>
    <div class="location-phones">Ana 0491 570 006 / Kate 0491 570 110</div>
  </section>

  <section class="details">
    <div class="details-note">By appointment only</div>
    <div class="details-links"><span>e: hello@corsetresses.com.au</span><span>w: www.corsetresses.com.au</span></div>
  </section>

  <footer class="site-footer">
    <div class="footer-copy">corsetresses © 2017<br>All Rights Reserved</div>
    <div class="footer-brand">
      <span class="brand-name">Corsetresses</span>
      <span class="brand-tag">hair &amp; body</span>
    </div>
    <div class="social-links" aria-label="Social media links"><span></span><span></span><span></span></div>
  </footer>

  <svg class="back-to-top" width="26" height="26" viewBox="0 0 26 26" aria-label="Back to top">
    <circle cx="13" cy="13" r="13" fill="#a54499"/>
    <polyline points="9.5,14.5 13,11 16.5,14.5" fill="none" stroke="#ffffff" stroke-width="1.8" stroke-linecap="round" stroke-linejoin="round"/>
  </svg>
</div>
</body>
</html>
```